MEDICAL CLINIC LETTERHEAD

Design is a letterhead for a non-profit medical center. The name of the clinic is VITARIDGE Community Health Center. Although the full name must be included, the community health center part is more of a description and should be less visible - i attached an example of what I mean by that (ATTACHED IMAGE IS AN EXAMPLE OF FONT SIZES NOT A DESIGN IDEA). Please design something modern, cool looking and unique because I can always download free templates.
Phone, email, website and etc will be added later.

Industry/Entity Type

MEDICAL

```html
<!DOCTYPE html>
<html lang="en">
<head>
<meta charset="UTF-8">
<title>VITARIDGE Community Health Center – Letterhead</title>
<link rel="stylesheet" href="https://fonts.googleapis.com/css2?family=Lato:wght@400;700&family=Montserrat:wght@400;500;700&family=Italianno&display=swap">
<style>
  :root {
    --navy: #1c2d4f;
    --gold: #ae9156;
    --ink: #3a3a3a;
    --ink-dark: #1e1e1e;
    --paper: #ffffff;
    --paper-edge: #f1f0f0;
    --backdrop: #e4e4e4;
  }
  * { margin: 0; padding: 0; box-sizing: border-box; }
  html, body {
    width: 1153px; height: 1200px; overflow: hidden;
    background: var(--backdrop);
  }
  .letterhead {
    position: absolute; left: 156px; top: 12px;
    width: 840px; height: 1176px;
    background: radial-gradient(ellipse at 55% 35%, var(--paper) 0%, var(--paper) 25%, var(--paper-edge) 80%);
    box-shadow: 0 4px 18px rgba(0,0,0,0.18);
    overflow: hidden;
    font-family: "Lato", Arial, sans-serif;
    color: var(--ink);
  }
  .brand-name {
    position: absolute; left: 46px; top: 86px;
    font-family: "Montserrat", Arial, sans-serif;
    font-weight: 700; font-size: 40px; letter-spacing: 1px;
    color: var(--navy);
  }
  .contact {
    position: absolute; left: 574px; top: 49px; height: 95px;
    border-left: 1.5px solid var(--gold);
    padding-left: 13px;
    font-family: "Montserrat", Arial, sans-serif;
    font-size: 14.5px; color: var(--ink-dark);
  }
  .contact-name { line-height: 18px; margin-top: -3px; font-weight: 500; }
  .contact-list { list-style: none; margin-top: 6px; }
  .contact-list li { display: flex; align-items: center; line-height: 20px; }
  .contact-list svg { width: 14px; height: 12px; margin-right: 10px; fill: var(--gold); }
  .letter {
    position: absolute; left: 64px; top: 260px; width: 711px;
    font-size: 15px; line-height: 18px;
  }
  .date { margin-bottom: 21px; }
  .recipient { margin-bottom: 20px; }
  .address { margin-bottom: 20px; }
  .salutation { font-weight: 700; font-size: 19px; margin-bottom: 18px; }
  .body-text p { text-align: justify; margin-bottom: 18px; }
  .closing { margin-top: 37px; }
  .signature {
    font-family: "Italianno", cursive;
    font-size: 46px; line-height: 50px; margin-top: 18px; margin-left: 4px;
    color: var(--ink-dark);
  }
  .footer-wave { position: absolute; left: 0; bottom: 0; width: 840px; height: 165px; }
</style>
</head>
<body>
  <main class="letterhead">
    <div class="brand-name">VITARIDGE</div>

    <div class="contact">
      <p class="contact-name">VITARIDGE Community<br>Health Center</p>
      <ul class="contact-list">
        <li><svg viewBox="0 0 14 12"><path d="M1 4 Q7 -1 13 4 L11 5 L10 3 Q7 2 4 3 L3 5 Z M3 6 H11 L12 11 H2 Z"/></svg>555-214-3790</li>
        <li><svg viewBox="0 0 14 12"><path d="M1 2 H13 V11 H1 Z M1.8 2.8 L7 7 L12.2 2.8" stroke="#fff" stroke-width="0.8"/></svg>hello@vitaridge-care.org</li>
        <li><svg viewBox="0 0 14 12"><circle cx="7" cy="6" r="5.5"/></svg>www.vitaridge-care.org</li>
      </ul>
    </div>

    <article class="letter">
      <p class="date">Feb-03-2022</p>
      <p class="recipient">Mr, Paul Hartley<br>President</p>
      <p class="address">Northfield Partners<br>48 Orchard Lane, Suite# 7<br>Brookvale, State, 240118</p>
      <p class="salutation">Dear Mr, Paul</p>
      <div class="body-text">
        <p>Lorem ipsum dolor sit amet, consectetur adipisicing elit, sed do eiusmod tempor incididunt ut labore et dolore magna aliqua. Ut enim ad minim veniam, quis nostrud exercitation ullamco laboris nisi ut aliquip ex ea commodo consequat. Duis aute irure dolor in reprehenderit in voluptate velit esse cillum dolore eu fugiat nulla pariatur.</p>
        <p>Lorem ipsum dolor sit amet, consectetur adipisicing elit, sed do eiusmod tempor incididunt ut labore et dolore magna aliqua. Ut enim ad minim veniam, quis nostrud exercitation ullamco laboris nisi ut aliquip ex ea commodo consequat. Duis aute irure dolor in reprehenderit in voluptate velit esse cillum dolore eu fugiat nulla pariatur.</p>
        <p>Lorem ipsum dolor sit amet, consectetur adipisicing elit, sed do eiusmod tempor incididunt ut labore et dolore magna aliqua. Ut enim ad minim veniam, quis nostrud exercitation ullamco laboris nisi ut aliquip ex ea commodo consequat.</p>
        <p>Excepteur sint occaecat cupidatat non proident, sunt in culpa qui officia deserunt mollit anim id est laborum. re et dolore magnam aliquam quaerat voluptatem.</p>
      </div>
      <p class="closing">Regards</p>
      <p class="signature">Daniel Reyes</p>
    </article>

    <svg class="footer-wave" viewBox="0 0 840 165" preserveAspectRatio="none" aria-hidden="true">
      <path fill="var(--navy)" d="M0 0 C90 80 180 110 300 106 C420 102 560 55 680 58 C740 60 800 80 840 100 L840 165 L0 165 Z"/>
      <path fill="var(--gold)" d="M102 60 C180 95 260 96 330 90 C450 75 560 52 640 55 C700 57 750 70 787 84 C740 72 690 63 640 63 C560 63 450 87 330 99 C250 106 170 96 102 60 Z"/>
    </svg>
  </main>
</body>
</html>
```